Talents and colours poster for home office

The objective is to illustrate/communicate and remember 5 talents and 4 colours of the personality.

The infographic will be hanged on the wall of an home office. It need to be simple and clear. Illustrations and pictograms can be used. It can be artistic.

Here's the content:

5 talents,scaling in priority from #1 to #5
Ideation / creativity
Winning other over / charisma
Adaptability
Positivity
Empathy

In the files there is a description of what those mean.

You have to include 4 colours, scaling in priority from #1 to #4
Yellow
Green
Red
Blue

I made a sketch just for fun... and to show why I need professionnal skills :)

THX

Industry/Entity Type

Office

Requirements
Should not have
• offensive materials

```html
<!DOCTYPE html>
<html lang="en">
<head>
<meta charset="utf-8">
<title>Talents and Colours</title>
<link rel="stylesheet" href="https://fonts.googleapis.com/css2?family=Bebas+Neue&display=swap">
<style>
  :root {
    --poster-bg: #1f1d1b;
    --yellow-light: #f8ee4f;
    --yellow-dark: #f4e322;
    --green-light: #9fc857;
    --green-dark: #8bbb3e;
    --red-light: #e94a3b;
    --red-dark: #e22f2b;
    --navy-light: #45599b;
    --navy-dark: #324888;
    --sky-light: #82a1d2;
    --sky-dark: #6f90c5;
    --ink-dark: #1c1c1a;
    --ink-light: #ffffff;
  }
  html, body {
    margin: 0;
    padding: 0;
    width: 929px;
    height: 1200px;
    overflow: hidden;
    background: var(--poster-bg);
  }
  .poster {
    position: relative;
    width: 929px;
    height: 1200px;
    background: var(--poster-bg);
    box-sizing: border-box;
    padding: 128px 57px 0;
  }
  .talent-list {
    list-style: none;
    margin: 0;
    padding: 0;
    display: flex;
    flex-direction: column;
    gap: 40px;
  }
  .talent {
    height: 163px;
    border-radius: 22px;
    display: flex;
    align-items: center;
    justify-content: center;
    font-family: "Bebas Neue", "Oswald", sans-serif;
    font-size: 50px;
    letter-spacing: 0.5px;
    box-shadow: 0 8px 6px rgba(0, 0, 0, 0.55);
  }
  .talent--yellow {
    background: linear-gradient(to bottom, var(--yellow-light) 0 50%, var(--yellow-dark) 50% 100%);
    color: var(--ink-dark);
  }
  .talent--green {
    background: linear-gradient(to bottom, var(--green-light) 0 50%, var(--green-dark) 50% 100%);
    color: var(--ink-dark);
  }
  .talent--red {
    background: linear-gradient(to bottom, var(--red-light) 0 50%, var(--red-dark) 50% 100%);
    color: var(--ink-light);
  }
  .talent--navy {
    background: linear-gradient(to bottom, var(--navy-light) 0 50%, var(--navy-dark) 50% 100%);
    color: var(--ink-light);
  }
  .talent--sky {
    background: linear-gradient(to bottom, var(--sky-light) 0 50%, var(--sky-dark) 50% 100%);
    color: var(--ink-light);
  }
</style>
</head>
<body>
  <main class="poster">
    <ol class="talent-list">
      <li class="talent talent--yellow">Ideation / Creativity</li>
      <li class="talent talent--green">Winning Other Over / Charisma</li>
      <li class="talent talent--red">Adaptability</li>
      <li class="talent talent--navy">Positivity</li>
      <li class="talent talent--sky">Empathy</li>
    </ol>
  </main>
</body>
</html>
```